Kovát Lillas Physiotherapy Business Card Vienna

We need a business card design for a newly created Physiotherapy company based in Vienna Austria.
We seek a simple, modern, minimalist design without too much color variation. The font should look young/fresh, but definitely not childish or so. Since we are a starting Business, we currently haven't got a logo, if you feel like a logo would fit your design, feel free to use one, but it's not necessary.
Target Market(s)
Healthcare, young and elderly people with mobility issues
Industry/Entity Type
Health And Wellness
Contact Information for Business Card
Name: Lilla Kovát
Title description: Physiotherapist
Phone num: +43 664 2951 4086
e-mail: lilla.praxis@bluemail.example
Colors
Designer to choose colors to be used in the design.
Requirements
Must have
- Final design language must be in German, basically, the Title Description needs to be "Physiotherapeutin" the other details remain as in the English Language.
Nice to have
- Simple, modern, minimalist design
Should not have
- too many colors, Obvious use of a skeleton, skull, spline

```html
<!DOCTYPE html>
<html lang="de">
<head>
<meta charset="utf-8">
<title>Lilla Kovát – Physiotherapeutin</title>
<link rel="stylesheet" href="https://fonts.googleapis.com/css2?family=Kaushan+Script&family=EB+Garamond&family=Arimo&display=swap">
<style>
  :root {
    --forest: #386b04;
    --lime: #cce68a;
    --mist: #e2e2e2;
    --paper: #ffffff;
  }
  * { margin: 0; padding: 0; box-sizing: border-box; }
  html, body {
    width: 1200px;
    height: 960px;
    overflow: hidden;
    background: var(--paper);
  }
  .canvas {
    position: relative;
    width: 1200px;
    height: 960px;
  }
  .business-card {
    position: absolute;
    left: 114px;
    top: 202px;
    width: 972px;
    height: 555px;
    overflow: hidden;
    background: var(--forest);
  }
  .card-waves {
    position: absolute;
    inset: 0;
    width: 100%;
    height: 100%;
  }
  .wave-accent { fill: var(--lime); }
  .wave-field { fill: var(--mist); }
  .holder-name {
    position: absolute;
    left: 28px;
    top: 230px;
    font-family: "Kaushan Script", cursive;
    font-size: 112px;
    line-height: 1;
    color: var(--forest);
    white-space: nowrap;
    letter-spacing: -2px;
  }
  .holder-title {
    position: absolute;
    left: 55px;
    top: 366px;
    font-family: "EB Garamond", serif;
    font-size: 50px;
    line-height: 1;
    color: var(--forest);
    white-space: nowrap;
  }
  .contact-list {
    position: absolute;
    left: 59px;
    top: 440px;
    list-style: none;
  }
  .contact-item {
    display: flex;
    align-items: center;
    height: 30px;
    margin-bottom: 8px;
    font-family: "Arimo", sans-serif;
    font-size: 24px;
    color: var(--forest);
  }
  .contact-icon {
    width: 30px;
    height: 30px;
    margin-right: 18px;
    flex: none;
  }
  .contact-icon .disc { fill: var(--forest); }
  .contact-icon .glyph { fill: var(--paper); }
</style>
</head>
<body>
<main class="canvas">
  <section class="business-card">
    <svg class="card-waves" viewBox="0 0 972 555" preserveAspectRatio="none" aria-hidden="true">
      <path class="wave-accent" d="M0,93 C80,70 150,61 220,61 C520,60 760,300 874,555 L0,555 Z"/>
      <path class="wave-field" d="M0,130 C80,112 150,102 229,102 C520,102 740,320 868,555 L0,555 Z"/>
    </svg>

    <h1 class="holder-name">Lilla Kovát</h1>
    <p class="holder-title">Physiotherapeutin</p>

    <ul class="contact-list">
      <li class="contact-item">
        <svg class="contact-icon" viewBox="0 0 30 30" aria-hidden="true">
          <circle class="disc" cx="15" cy="15" r="15"/>
          <path class="glyph" d="M10.5 7.5l2.6 3.4-1.6 1.8c.9 2 2.6 3.8 4.6 4.8l1.8-1.6 3.4 2.6-1.6 2.6c-5.8-.6-10.4-5.2-11-11z"/>
        </svg>
        <span>+43 664 2951 4086</span>
      </li>
      <li class="contact-item">
        <svg class="contact-icon" viewBox="0 0 30 30" aria-hidden="true">
          <circle class="disc" cx="15" cy="15" r="15"/>
          <path class="glyph" d="M8 10h14v10H8z"/>
          <path d="M8 10l7 6 7-6M8 20l5.2-5M22 20l-5.2-5" fill="none" stroke="#386b04" stroke-width="1.4"/>
        </svg>
        <span>lilla.praxis@bluemail.example</span>
      </li>
    </ul>
  </section>
</main>
</body>
</html>
```